Need webdesign for service company that provides Car hiring service and transit service

We need a web design for a company that provides airport transit services and transport services including Limo, Corporate cars, Disability transit, Family transit service. We need is a simple and professional design.

Below is site which we like and also offer the same service http://www.ridelarkway.com.au/
Updates

Project Deadline Extended
Reason: Waiting for the Feedback from multiple stakeholders. Need the time to select and approve the design

Target Market(s)

Tourism, Travel

Industry/Entity Type

Airport

Number of Pages Required

3 page

Font styles to use
Decorative
Script

Requirements
Must have
• Simple and Professional, Site we like http://www.ridelarkway.com.au/ and also need to mobile friendly
Should not have
• Shouldn't have too many images

```html
<!DOCTYPE html>
<html lang="en">
<head>
<meta charset="utf-8">
<title>RIDEWELL – Private &amp; Business Transport</title>
<link href="https://fonts.googleapis.com/css2?family=Lato:wght@300;400;700&family=Open+Sans:wght@300;700&family=Sorts+Mill+Goudy&display=swap" rel="stylesheet">
<style>
  :root{
    --ink:#111111;
    --black:#000000;
    --white:#ffffff;
    --grey-text:#666666;
    --panel:#e6e6e6;
    --button:#7a787a;
    --field-border:#d6d6d6;
    --hero-dark:#1a0f08;
    --hero-amber:#d98a12;
    --hero-gold:#f2c230;
    --hero-violet:#a06ad0;
  }
  *{box-sizing:border-box;margin:0;padding:0}
  html,body{width:1060px;height:1200px;overflow:hidden;background:var(--white)}
  body{position:relative;font-family:'Lato',sans-serif;color:var(--ink)}

  .top-rule{position:absolute;left:0;top:0;width:1060px;height:5px;background:var(--black)}
  .site-header{position:absolute;left:0;top:5px;width:1060px;height:109px;background:var(--white);
    box-shadow:0 4px 5px -2px rgba(0,0,0,.35)}
  .brand{position:absolute;left:90px;top:33px;display:flex;align-items:center;gap:12px}
  .brand-mark{width:22px;height:22px;background:var(--ink)}
  .brand-name{font-family:'Lato',sans-serif;font-weight:700;font-size:34px;letter-spacing:.5px;color:var(--ink)}

  .diamond-btn{position:absolute;width:46px;height:46px}
  .phone-btn{left:685px;top:33px}
  .phone-number{position:absolute;left:742px;top:45px;font-weight:700;font-size:18px;color:var(--ink)}
  .menu-btn{left:873px;top:33px}
  .search-btn{left:927px;top:33px}

  .tagline-block{position:absolute;left:370px;top:143px;width:320px;text-align:center}
  .tagline-title{font-family:'Sorts Mill Goudy',serif;font-size:32px;line-height:36px;color:var(--ink)}
  .tagline-title .amp{font-size:38px}
  .tagline-rule{height:1px;background:var(--ink);margin-top:-2px}
  .tagline-sub{font-weight:300;font-size:18px;color:var(--grey-text);margin-top:0}

  .hero{position:absolute;left:0;top:235px;width:1060px;height:487px;
    background:
      linear-gradient(160deg,rgba(160,106,208,.55) 0%,rgba(160,106,208,0) 22%),
      radial-gradient(ellipse at 55% 45%,var(--hero-gold) 0%,var(--hero-amber) 30%,rgba(80,40,10,.9) 60%,var(--hero-dark) 85%);}

  .quote-box{position:absolute;left:87px;top:335px;width:311px;height:288px;background:var(--black)}
  .quote-title{position:absolute;left:0;top:17px;width:100%;text-align:center;color:var(--white);font-weight:700;font-size:21px}
  .field{position:absolute;left:18px;width:274px;background:var(--white);display:flex;align-items:center}
  .field-icon{width:29px;height:100%;border-right:1px solid var(--field-border);display:flex;align-items:center;justify-content:center}
  .field-text{padding-left:11px;font-size:10.5px;color:var(--ink)}
  .field-origin{top:63px;height:34px}
  .field-destination{top:109px;height:34px}
  .field-options{top:155px;height:52px}
  .option-lines{padding-left:11px;font-size:10.5px;line-height:20px}
  .add-stop{display:flex;align-items:center;gap:7px}
  .plus-box{width:14px;height:14px;border:1px solid #bbb;display:flex;align-items:center;justify-content:center;font-size:11px;font-weight:700}
  .estimate-btn{position:absolute;left:18px;top:228px;width:274px;height:38px;background:var(--button);
    color:var(--white);font-weight:700;font-size:17px;text-align:center;line-height:38px}

  .about{position:absolute;left:89px;top:776px;width:436px}
  .about-heading{font-family:'Open Sans',sans-serif;font-weight:300;font-size:26px;color:var(--ink)}
  .about-heading strong{font-weight:700}
  .about p{font-size:12px;line-height:23px;color:var(--ink);letter-spacing:.15px;margin-top:11px}
  .about p:first-of-type{margin-top:12px}

  .services{position:absolute;left:555px;top:762px;width:418px;height:357px;background:var(--panel)}
  .service{position:absolute;width:200px;text-align:center}
  .service svg{display:block;margin:0 auto}
  .service-label{font-weight:700;font-size:15px;margin-top:14px;color:var(--ink)}
  .svc-corporate{left:0;top:27px}
  .svc-limo{left:199px;top:27px}
  .svc-disability{left:0;top:201px}
  .svc-family{left:199px;top:201px}

  .site-footer{position:absolute;left:0;top:1159px;width:1060px;height:41px;background:var(--black)}
  .copyright{position:absolute;left:89px;top:13px;color:var(--white);font-size:12px}
  .social{position:absolute;top:9px;width:24px;height:24px}
  .social-a{left:888px}.social-b{left:918px}.social-c{left:948px}
</style>
</head>
<body>
  <div class="top-rule"></div>
  <header class="site-header">
    <div class="brand"><span class="brand-mark"></span><span class="brand-name">RIDEWELL</span></div>

    <svg class="diamond-btn phone-btn" viewBox="0 0 46 46" aria-label="Phone">
      <rect x="9" y="9" width="28" height="28" transform="rotate(45 23 23)" fill="none" stroke="#111" stroke-width="1.6"/>
      <path d="M17 16c1-1 2-1 3 0l2 3c.5 1 0 2-1 2.5 1 2 2.5 3.5 4.5 4.5.5-1 1.5-1.5 2.5-1l3 2c1 1 1 2 0 3-3 3-8 0-11-3s-6-8-3-11z" fill="#111"/>
    </svg>
    <div class="phone-number">123 456 7890</div>

    <svg class="diamond-btn menu-btn" viewBox="0 0 46 46" aria-label="Menu">
      <rect x="9" y="9" width="28" height="28" transform="rotate(45 23 23)" fill="none" stroke="#111" stroke-width="1.6"/>
      <path d="M15 17.5h16M15 23h16M15 28.5h16" stroke="#111" stroke-width="2.6" stroke-linecap="round"/>
    </svg>
    <svg class="diamond-btn search-btn" viewBox="0 0 46 46" aria-label="Search">
      <rect x="9" y="9" width="28" height="28" transform="rotate(45 23 23)" fill="none" stroke="#111" stroke-width="1.6"/>
      <circle cx="21.5" cy="21.5" r="5.5" fill="none" stroke="#111" stroke-width="2.2"/>
      <path d="M25.5 25.5l4.5 4.5" stroke="#111" stroke-width="2.4" stroke-linecap="round"/>
    </svg>
  </header>

  <div class="tagline-block">
    <div class="tagline-title">Private <span class="amp">&amp;</span> Business</div>
    <div class="tagline-rule"></div>
    <div class="tagline-sub">Personalised Transport Services</div>
  </div>

  <section class="hero" role="img" aria-label="Night-time photo of a dark car in motion with amber and violet light trails"></section>

  <form class="quote-box">
    <div class="quote-title">GET INSTANT QUOTE</div>
    <div class="field field-origin">
      <div class="field-icon"><svg width="12" height="12"><circle cx="6" cy="6" r="4.5" fill="none" stroke="#111" stroke-width="1.2"/></svg></div>
      <div class="field-text">Origin ( Public Location Or Exact Address )</div>
    </div>
    <div class="field field-destination">
      <div class="field-icon"><svg width="10" height="14" viewBox="0 0 10 14"><path d="M5 0a5 5 0 0 0-5 5c0 4 5 9 5 9s5-5 5-9a5 5 0 0 0-5-5z" fill="#111"/><circle cx="5" cy="5" r="1.8" fill="#fff"/></svg></div>
      <div class="field-text">Destination ( Public Location Or Exact Address )</div>
    </div>
    <div class="field field-options">
      <div class="field-icon"><svg width="12" height="12"><circle cx="6" cy="6" r="4.5" fill="none" stroke="#111" stroke-width="1.2"/></svg></div>
      <div class="option-lines">
        <div>Show other vehicles</div>
        <div class="add-stop"><span class="plus-box">+</span>Add Stops</div>
      </div>
    </div>
    <div class="estimate-btn">ESTIMATE FARE</div>
  </form>

  <section class="about">
    <h2 class="about-heading">ABOUT <strong>US</strong></h2>
    <p>Fusce a lorem felis. Nulla quis tellus vulputate, pellentesque tortor in, dictum ligula. Ut pretium sem elit, quis luctus eros blandit sed. Mauris nec lacus elementum, vulputate orci sed, ullamcorper nulla. Etiam tempor lorem quis metus imperdiet aliquet. Vestibulum at mi risus. Sed mattis maximus tristique. Vivamus sollicitudin tellus sed velit accumsan, sed iaculis ligula dignissim. Maecenas accumsan ut dui vel commodo. Integer varius tortor at ipsum efficitur lobortis. Ut posuere in dui nec bibendum lectus bibendum est iaculis dignissim.</p>
    <p>Fusce a lorem felis. Nulla quis tellus vulputate, pellentesque tortor in, dictum ligula. Ut pretium sem elit, quis luctus eros blandit sed. Mauris nec lacus elementum, vulputate orci sed, ullamcorper nulla. Etiam tempor lorem quis metus imperdiet aliquet. Vestibulum at mi risus. Sed mattis maximus tristique. Vivamus sollicitudin tellus sed velit accumsan, sed iaculis ligula dignissim.</p>
  </section>

  <section class="services">
    <div class="service svc-corporate">
      <svg width="98" height="98" viewBox="0 0 98 98" aria-label="Car icon">
        <rect x="19" y="19" width="60" height="60" transform="rotate(45 49 49)" fill="#fff" stroke="#000" stroke-width="3.5"/>
        <path d="M25 53v-5l5-1 6-5h18l7 5 10 1 2 5z" fill="#111"/>
        <path d="M38 44h7v4h-10zM47 44h6l4 4h-10z" fill="#fff"/>
        <circle cx="34" cy="54" r="3.5" fill="#111" stroke="#fff" stroke-width="1.5"/>
        <circle cx="64" cy="54" r="3.5" fill="#111" stroke="#fff" stroke-width="1.5"/>
      </svg>
      <div class="service-label">CORPORATE CARS</div>
    </div>
    <div class="service svc-limo">
      <svg width="98" height="98" viewBox="0 0 98 98" aria-label="Limousine icon">
        <rect x="19" y="19" width="60" height="60" transform="rotate(45 49 49)" fill="#fff" stroke="#000" stroke-width="3.5"/>
        <path d="M36 40h26l3 7h3v3h-2v9h-5v-3H40v3h-5v-9h-2v-3h3z" fill="#111"/>
        <rect x="38" y="42" width="22" height="5" fill="#fff"/>
        <path d="M44 50v6M47 50v6M50 50v6M53 50v6" stroke="#fff" stroke-width="1.2"/>
      </svg>
      <div class="service-label">LIMO SERVICE</div>
    </div>
    <div class="service svc-disability">
      <svg width="98" height="98" viewBox="0 0 98 98" aria-label="Wheelchair icon">
        <rect x="19" y="19" width="60" height="60" transform="rotate(45 49 49)" fill="#fff" stroke="#000" stroke-width="3.5"/>
        <circle cx="45" cy="34" r="3" fill="#111"/>
        <path d="M45 39v10h10l4 9" fill="none" stroke="#111" stroke-width="3" stroke-linecap="round"/>
        <path d="M41 46a8 8 0 1 0 12 9" fill="none" stroke="#111" stroke-width="2.6"/>
      </svg>
      <div class="service-label">DISABILITY TRANSIT</div>
    </div>
    <div class="service svc-family">
      <svg width="98" height="98" viewBox="0 0 98 98" aria-label="Bus and family icon">
        <rect x="19" y="19" width="60" height="60" transform="rotate(45 49 49)" fill="#fff" stroke="#000" stroke-width="3.5"/>
        <rect x="34" y="38" width="20" height="20" rx="3" fill="#111"/>
        <rect x="37" y="42" width="14" height="7" fill="#fff"/>
        <rect x="36" y="58" width="4" height="3" fill="#111"/><rect x="48" y="58" width="4" height="3" fill="#111"/>
        <circle cx="58" cy="48" r="1.6" fill="#111"/><rect x="57" y="50.5" width="2.4" height="7" fill="#111"/>
        <circle cx="62" cy="50" r="1.4" fill="#111"/><rect x="61" y="52" width="2" height="5.5" fill="#111"/>
        <circle cx="66" cy="48" r="1.6" fill="#111"/><rect x="65" y="50.5" width="2.4" height="7" fill="#111"/>
      </svg>
      <div class="service-label">FAMILY TRANSIT SERVICE</div>
    </div>
  </section>

  <footer class="site-footer">
    <div class="copyright">Copyright © 2017 RIDEWELL. All Rights Reserved.</div>
    <svg class="social social-a" viewBox="0 0 24 24" aria-label="Social link"><rect x="5" y="5" width="14" height="14" transform="rotate(45 12 12)" fill="none" stroke="#fff" stroke-width="1.2"/></svg>
    <svg class="social social-b" viewBox="0 0 24 24" aria-label="Social link"><rect x="5" y="5" width="14" height="14" transform="rotate(45 12 12)" fill="none" stroke="#fff" stroke-width="1.2"/></svg>
    <svg class="social social-c" viewBox="0 0 24 24" aria-label="Social link"><rect x="5" y="5" width="14" height="14" transform="rotate(45 12 12)" fill="none" stroke="#fff" stroke-width="1.2"/></svg>
  </footer>
</body>
</html>
```